Create modern and sleek business card for luxury real estate company

We're a "boutique" real estate office looking for a design that gets across a highly modern luxury brand. Blacks and whites are probably the best colors unless we try a silver foil for the logo. I've attached a version of our current logo here. I'd like to swap out the current font on there with Gotham Light Regular.

I'm looking to have one side of the card have the logo with the space for our agents info on the other side.

Target Market(s)

Young professionals in a "luxury" headspace

Industry/Entity Type

Real estate

Contact Information for Business Card

A place for agent name, cell number, website. The slogan "Quietly Refining Modern Homes".

Font styles to use
Other font styles liked:
• Gotham Regular

Colors

Designer to choose only greyscale colors for use in the design.

Requirements
Must have
• Matte black as the background color. Clean lines and use of contrast. A specific design aspect that will use silver foil.
Nice to have
• Up in the air on integrating a QR code
Should not have
• Any houses or other real estate related design (ex: a clip art house)

```html
<!DOCTYPE html>
<html lang="en">
<head>
<meta charset="utf-8">
<title>Aldmere Realty – Business Card</title>
<link href="https://fonts.googleapis.com/css2?family=Montserrat:wght@300;400;600&display=swap" rel="stylesheet">
<style>
  :root {
    --stage: #474747;
    --card: #0d0d0d;
    --card-edge: #1a1a1a;
    --silver: #e6e6e6;
    --muted: #8a8a8a;
    --rule: #5a5a5a;
    --gloss-a: #1c1c1c;
    --gloss-b: #050505;
  }
  * { box-sizing: border-box; margin: 0; padding: 0; }
  html, body { width: 1200px; height: 801px; overflow: hidden; }
  body {
    background: var(--stage);
    font-family: "Montserrat", Arial, sans-serif;
    color: var(--silver);
    position: relative;
  }
  .card {
    position: absolute;
    top: 252px;
    width: 525px;
    height: 300px;
    background: var(--card);
    border: 1px solid var(--card-edge);
    overflow: hidden;
  }
  .card--front { left: 50px; }
  .card--back { left: 625px; }

  /* front side */
  .gloss-accent {
    position: absolute;
    right: -40px;
    top: -70px;
    width: 300px;
    height: 300px;
    border-radius: 50%;
    background: radial-gradient(circle at 40% 40%, var(--gloss-a), var(--gloss-b) 70%);
  }
  .agent-info {
    position: absolute;
    left: 36px;
    top: 34px;
    width: 300px;
  }
  .brand {
    display: flex;
    align-items: center;
    gap: 10px;
    margin-bottom: 22px;
  }
  .brand__dot {
    width: 34px;
    height: 34px;
    border: 1.5px solid var(--silver);
    border-radius: 50%;
    flex: none;
  }
  .brand__name {
    font-weight: 400;
    font-size: 17px;
    letter-spacing: 2.5px;
    text-transform: uppercase;
    line-height: 1.15;
    color: var(--silver);
  }
  .agent-name {
    font-weight: 600;
    font-size: 17px;
    letter-spacing: 0.5px;
    text-transform: uppercase;
  }
  .agent-title {
    font-weight: 400;
    font-size: 12px;
    color: var(--muted);
    margin-top: 2px;
  }
  .divider {
    width: 48px;
    height: 1px;
    background: var(--rule);
    margin: 14px 0 12px;
  }
  .contact { list-style: none; }
  .contact li {
    display: flex;
    align-items: center;
    gap: 8px;
    font-size: 12.5px;
    font-weight: 400;
    line-height: 21px;
  }
  .contact svg { width: 11px; height: 11px; flex: none; fill: var(--muted); }
  .slogan {
    font-size: 12.5px;
    font-weight: 400;
  }

  /* back side */
  .pattern-field {
    position: absolute;
    inset: 0;
    background: linear-gradient(135deg, #070707 0%, #141414 50%, #1f1f1f 100%);
  }
  .brand--back {
    position: absolute;
    right: 48px;
    top: 150px;
    margin: 0;
  }
  .brand--back .brand__dot { width: 40px; height: 40px; }
  .brand--back .brand__name { font-size: 20px; }
</style>
</head>
<body>

<section class="card card--front" aria-label="Agent side">
  <div class="gloss-accent" role="img" aria-label="Large glossy brand emblem in spot gloss"></div>
  <div class="agent-info">
    <div class="brand">
      <span class="brand__dot"></span>
      <span class="brand__name">Aldmere<br>Realty</span>
    </div>
    <p class="agent-name">Daniel Harrow</p>
    <p class="agent-title">President</p>
    <div class="divider"></div>
    <ul class="contact">
      <li>
        <svg viewBox="0 0 24 24" aria-hidden="true"><path d="M6.6 10.8a15.1 15.1 0 0 0 6.6 6.6l2.2-2.2c.3-.3.7-.4 1-.2 1.1.4 2.3.6 3.6.6.6 0 1 .4 1 1V20c0 .6-.4 1-1 1A17 17 0 0 1 3 4c0-.6.4-1 1-1h3.5c.6 0 1 .4 1 1 0 1.3.2 2.5.6 3.6.1.3 0 .7-.2 1z"/></svg>
        555-010-4821
      </li>
      <li>
        <svg viewBox="0 0 24 24" aria-hidden="true"><path d="M2 5h20v14H2z"/></svg>
        dharrow@aldmererealty.com
      </li>
      <li>
        <svg viewBox="0 0 24 24" aria-hidden="true"><circle cx="12" cy="12" r="10"/></svg>
        www.aldmererealty.com
      </li>
    </ul>
    <div class="divider"></div>
    <p class="slogan">Quietly Refining Modern Homes</p>
  </div>
</section>

<section class="card card--back" aria-label="Brand side">
  <div class="pattern-field" role="img" aria-label="Repeating glossy brand emblem pattern in spot gloss on matte black"></div>
  <div class="brand brand--back">
    <span class="brand__dot"></span>
    <span class="brand__name">Aldmere<br>Realty</span>
  </div>
</section>

</body>
</html>
```